Working Capital graphics

Our business advisory firm requires 9 images to be re-created and improved in the branding of our business.

The 9 images have been uploaded below and the colours and branding of the business can be found at the website www.tallowmereadvisory.com.au

```html
<!DOCTYPE html>
<html lang="en">
<head>
<meta charset="utf-8">
<title>Inventories – Inventory Drivers</title>
<link rel="stylesheet" href="https://fonts.googleapis.com/css2?family=Merriweather:ital,wght@0,400;1,400;1,700;1,900&display=swap">
<style>
  :root {
    --canvas: #ffffff;
    --brand-orange: #f6921e;
    --brand-maroon: #85161d;
    --ink: #1a1a1a;
    --paper: #ffffff;
  }
  html, body {
    margin: 0;
    padding: 0;
    width: 1200px;
    height: 1000px;
    overflow: hidden;
    background: var(--canvas);
  }
  .chart {
    display: block;
    width: 1200px;
    height: 1000px;
    font-family: "Merriweather", Georgia, serif;
  }
  .panel { fill: var(--brand-orange); }
  .title { fill: var(--paper); font-style: italic; font-weight: 400; font-size: 34px; }
  .column-head { fill: var(--paper); font-size: 16px; font-weight: 400; text-anchor: middle; }
  .connector { stroke: var(--paper); stroke-width: 1.6; fill: none; }
  .box { fill: var(--paper); }
  .root-label { fill: var(--ink); font-style: italic; font-weight: 700; font-size: 20px; text-anchor: middle; }
  .group-label { fill: var(--ink); font-style: italic; font-weight: 700; font-size: 18px; text-anchor: middle; }
  .group-badge { fill: var(--brand-maroon); }
  .group-number { fill: var(--paper); font-style: italic; font-weight: 400; font-size: 30px; text-anchor: middle; }
  .sub-label { fill: var(--ink); font-style: italic; font-weight: 700; font-size: 15.5px; text-anchor: middle; }
</style>
</head>
<body>
<svg class="chart" viewBox="0 0 1200 1000" xmlns="http://www.w3.org/2000/svg" role="img" aria-label="Inventory drivers grouped into planning, procurement, fulfilment and product range">
  <rect class="panel" x="54" y="61" width="1099" height="878"/>

  <text class="title" x="120" y="174">Inventories</text>
  <text class="column-head" x="566" y="177">Driver Group</text>
  <text class="column-head" x="914" y="177">Sub-groups</text>

  <!-- root -->
  <rect class="box" x="120" y="449" width="205" height="108"/>
  <text class="root-label" x="222" y="498">Inventory</text>
  <text class="root-label" x="222" y="523">Drivers</text>

  <!-- trunk -->
  <path class="connector" d="M343 502 H399 M399 296 V783 M399 296 H440 M399 475 H440 M399 626 H440 M399 783 H440"/>

  <!-- branch connectors -->
  <path class="connector" d="M665 296 H697 M697 218 V372 M697 218 H729 M697 269 H729 M697 321 H729 M697 372 H729"/>
  <path class="connector" d="M665 475 H697 M697 425 V527 M697 425 H729 M697 476 H729 M697 527 H729"/>
  <path class="connector" d="M665 626 H697 M697 580 V674 M697 580 H729 M697 627 H729 M697 674 H729"/>
  <path class="connector" d="M665 783 H697 M697 735 V837 M697 735 H729 M697 784 H729 M697 837 H729"/>

  <!-- driver groups -->
  <g class="group">
    <rect class="box" x="452" y="274" width="213" height="43"/>
    <circle class="group-badge" cx="452" cy="296" r="27"/>
    <text class="group-number" x="451" y="307">10</text>
    <text class="group-label" x="565" y="302">Planning</text>
  </g>
  <g class="group">
    <rect class="box" x="452" y="454" width="213" height="43"/>
    <circle class="group-badge" cx="452" cy="475" r="27"/>
    <text class="group-number" x="451" y="486">11</text>
    <text class="group-label" x="565" y="481">Procurement</text>
  </g>
  <g class="group">
    <rect class="box" x="452" y="605" width="213" height="43"/>
    <circle class="group-badge" cx="452" cy="626" r="27"/>
    <text class="group-number" x="451" y="637">12</text>
    <text class="group-label" x="565" y="633">Fulfilment</text>
  </g>
  <g class="group">
    <rect class="box" x="452" y="762" width="213" height="43"/>
    <circle class="group-badge" cx="452" cy="783" r="27"/>
    <text class="group-number" x="451" y="794">13</text>
    <text class="group-label" x="565" y="790">Product Range</text>
  </g>

  <!-- sub-groups -->
  <g class="sub">
    <rect class="box" x="729" y="204" width="336" height="29"/><text class="sub-label" x="897" y="224">Demand variability</text>
    <rect class="box" x="729" y="255" width="336" height="29"/><text class="sub-label" x="897" y="275">Planning collaboration</text>
    <rect class="box" x="729" y="307" width="336" height="29"/><text class="sub-label" x="897" y="327">Information availability</text>
    <rect class="box" x="729" y="358" width="336" height="29"/><text class="sub-label" x="897" y="378">Inventory target setting</text>

    <rect class="box" x="729" y="411" width="336" height="29"/><text class="sub-label" x="897" y="431">Order quantities</text>
    <rect class="box" x="729" y="462" width="336" height="29"/><text class="sub-label" x="897" y="482">Supplier lead time variability</text>
    <rect class="box" x="729" y="513" width="336" height="29"/><text class="sub-label" x="897" y="533">Supplier quality variability</text>

    <rect class="box" x="729" y="566" width="336" height="29"/><text class="sub-label" x="897" y="586">Customer service leads</text>
    <rect class="box" x="729" y="613" width="336" height="29"/><text class="sub-label" x="897" y="633">Network structure</text>
    <rect class="box" x="729" y="660" width="336" height="29"/><text class="sub-label" x="897" y="680">Supplier quality variability</text>

    <rect class="box" x="729" y="721" width="336" height="29"/><text class="sub-label" x="897" y="741">Customer service leads</text>
    <rect class="box" x="729" y="770" width="336" height="29"/><text class="sub-label" x="897" y="790">Parts standardisation</text>
    <rect class="box" x="729" y="823" width="336" height="29"/><text class="sub-label" x="897" y="843">SKU proliferation</text>
  </g>
</svg>
</body>
</html>
```